Business Card and Simple Logo Desgin

New Zealand based start up company "Vesta Advisory LTD" requires business cards and simple logo design.

Card Content.

Vesta Advisory LTD

Rebecca Thornbury
CA, BMS (Hons)

r.thornbury@vestaadvisory.co.nz
PH +64 21 574 613

Target Market(s)

Corporate Business in IT, Finance and accounting.

Industry/Entity Type

Business

```html
<!DOCTYPE html>
<html lang="en">
<head>
<meta charset="utf-8">
<title>Vesta Advisory LTD – Business Card</title>
<link rel="stylesheet" href="https://fonts.googleapis.com/css2?family=Source+Sans+3:wght@400;600;700&display=swap">
<style>
  :root {
    --card-bg: #000000;
    --card-border: #7a7a7a;
    --brand-red: #ff0a2b;
    --accent-orange: #f27a1c;
    --text-grey: #cfcfcf;
    --font-main: "Source Sans 3", "Myriad Pro", Arial, sans-serif;
  }
  html, body {
    margin: 0;
    padding: 0;
    width: 1200px;
    height: 695px;
    overflow: hidden;
    background: var(--card-bg);
  }
  .card {
    position: relative;
    width: 1200px;
    height: 695px;
    box-sizing: border-box;
    background: var(--card-bg);
    border: 2px solid var(--card-border);
    font-family: var(--font-main);
    overflow: hidden;
  }
  .card__block {
    position: absolute;
    left: 0;
    width: 760px;
    text-align: center;
    margin: 0;
    line-height: 1;
    white-space: nowrap;
  }
  .brand-mark {
    top: 122px;
    font-size: 112px;
    font-weight: 600;
    color: var(--brand-red);
    letter-spacing: 1px;
  }
  .company-name {
    top: 322px;
    font-size: 47px;
    font-weight: 700;
    color: var(--brand-red);
    letter-spacing: 0.3px;
  }
  .person-name {
    top: 444px;
    font-size: 35px;
    font-weight: 700;
    color: var(--text-grey);
  }
  .person-credentials {
    top: 492px;
    font-size: 35px;
    font-weight: 400;
    color: var(--text-grey);
  }
  .contact {
    width: 716px;
    font-size: 33px;
    font-weight: 400;
    color: var(--text-grey);
  }
  .contact--email { top: 557px; }
  .contact--phone { top: 609px; }
  .side-rules {
    position: absolute;
    top: 0;
    right: 0;
    width: 200px;
    height: 695px;
  }
</style>
</head>
<body>
  <main class="card">
    <p class="card__block brand-mark">Vesta</p>
    <p class="card__block company-name">VESTA ADVISORY LTD</p>

    <p class="card__block person-name">Rebecca Thornbury</p>
    <p class="card__block person-credentials">CA, BMS (Hons)</p>

    <p class="card__block contact contact--email">r.thornbury@vestaadvisory.co.nz</p>
    <p class="card__block contact contact--phone">PH +64 21 574 613</p>

    <svg class="side-rules" viewBox="0 0 200 695" aria-hidden="true">
      <line x1="51" y1="0" x2="51" y2="695" stroke="var(--accent-orange)" stroke-width="2"/>
      <line x1="76" y1="0" x2="76" y2="695" stroke="var(--accent-orange)" stroke-width="2"/>
      <line x1="101" y1="0" x2="101" y2="695" stroke="var(--accent-orange)" stroke-width="2"/>
    </svg>
  </main>
</body>
</html>
```